Stationary design for boutique production house

We need a stationary design for our production house, 'Lorno Productions' based in Singapore. We produce microfilms as well as podcasts, talkshows and events. Our logo is a stylized icon of our director, who is also the executive producer and host of our programs, Lorno. Our main company colors are Red, Black and white. We would like a clean, minimalist design incorporating our existing company logo that conveys a sense of urbanism and elegance.

Logo and font files are attached. f

Target Market(s)

We focus on lifestyle media rather than entertainment.

Industry/Entity Type

Boutique

Font styles to use
Serif
Sans Serif

Colors
ec1f27
ffffff
000000

Requirements
Must have
• Our company logo and at least one of our company colors.
Nice to have
• Our address and contact information.
Should not have
• Changes made to the company logo (using only certain parts of it is fine though)

```html
<!DOCTYPE html>
<html lang="en">
<head>
<meta charset="utf-8">
<title>Lorno Productions – Business Cards</title>
<link href="https://fonts.googleapis.com/css2?family=Libre+Baskerville:wght@400;700&display=swap" rel="stylesheet">
<style>
  :root {
    --brand-red: #ec1f27;
    --brand-white: #ffffff;
    --brand-black: #000000;
    --backdrop: #e9e4dc;
    --card-shadow: rgba(0, 0, 0, 0.18);
  }
  * { box-sizing: border-box; margin: 0; padding: 0; }
  html, body {
    width: 1200px;
    height: 899px;
    overflow: hidden;
    background: var(--backdrop);
    font-family: "Libre Baskerville", Georgia, serif;
  }
  .stage {
    width: 1200px;
    height: 899px;
    display: flex;
    align-items: center;
    justify-content: center;
    gap: 110px;
  }
  .card {
    width: 300px;
    height: 525px;
    position: relative;
    box-shadow: 0 10px 30px var(--card-shadow);
    display: flex;
    flex-direction: column;
    align-items: center;
  }

  /* Brand lockup: plain circle above the name */
  .brand-lockup {
    display: flex;
    flex-direction: column;
    align-items: center;
  }
  .brand-lockup__circle {
    border-radius: 50%;
    flex: none;
  }
  .brand-lockup__name {
    font-weight: 400;
    letter-spacing: 0.04em;
    text-transform: uppercase;
    white-space: nowrap;
  }
  .brand-rule {
    height: 1px;
  }

  /* Front */
  .card--front {
    background: var(--brand-white);
    justify-content: center;
    padding-bottom: 30px;
  }
  .card--front .brand-lockup__circle {
    width: 130px;
    height: 130px;
    background: var(--brand-black);
  }
  .card--front .brand-lockup__name {
    margin-top: 22px;
    font-size: 18px;
    color: var(--brand-black);
  }
  .card--front .brand-rule {
    width: 160px;
    margin-top: 12px;
    background: var(--brand-black);
  }

  /* Back */
  .card--back {
    background: var(--brand-red);
    color: var(--brand-white);
    padding-top: 52px;
  }
  .card--back .brand-lockup__circle {
    width: 92px;
    height: 92px;
    background: var(--brand-white);
  }
  .card--back .brand-lockup__name {
    margin-top: 16px;
    font-size: 15px;
    color: var(--brand-white);
  }
  .card--back .brand-rule {
    width: 150px;
    margin-top: 10px;
    background: var(--brand-white);
  }
  .person {
    margin-top: 40px;
    text-align: center;
  }
  .person__name {
    font-size: 18px;
    font-weight: 700;
    letter-spacing: 0.03em;
    text-transform: uppercase;
  }
  .person__title {
    font-size: 13px;
    margin-top: 4px;
  }
  .divider {
    display: flex;
    align-items: center;
    width: 230px;
    margin-top: 10px;
  }
  .divider__line { flex: 1; height: 1px; background: var(--brand-white); }
  .divider__icon { width: 22px; height: 22px; margin: 0 6px; }
  .contact {
    margin-top: 12px;
    text-align: center;
    font-size: 13px;
    font-weight: 700;
    line-height: 1.6;
    list-style: none;
  }
  .contact__address { margin-bottom: 4px; }
  .closing-rule {
    width: 230px;
    height: 1px;
    background: var(--brand-white);
    margin-top: 16px;
  }
</style>
</head>
<body>
  <main class="stage">
    <section class="card card--front" aria-label="Card front">
      <div class="brand-lockup">
        <span class="brand-lockup__circle"></span>
        <span class="brand-lockup__name">Lorno Productions</span>
        <div class="brand-rule"></div>
      </div>
    </section>

    <section class="card card--back" aria-label="Card back">
      <div class="brand-lockup">
        <span class="brand-lockup__circle"></span>
        <span class="brand-lockup__name">Lorno Productions</span>
        <div class="brand-rule"></div>
      </div>

      <div class="person">
        <p class="person__name">Lorno Hale</p>
        <p class="person__title">President</p>
      </div>

      <div class="divider">
        <span class="divider__line"></span>
        <svg class="divider__icon" viewBox="0 0 22 22" aria-hidden="true">
          <circle cx="11" cy="11" r="10" fill="#ffffff"/>
          <path d="M11 5.5a3.6 3.6 0 0 0-3.6 3.6c0 2.7 3.6 6.6 3.6 6.6s3.6-3.9 3.6-6.6A3.6 3.6 0 0 0 11 5.5z" fill="#ec1f27"/>
          <circle cx="11" cy="9.1" r="1.3" fill="#ffffff"/>
        </svg>
        <span class="divider__line"></span>
      </div>

      <ul class="contact">
        <li>Street Address Line 1</li>
        <li class="contact__address">Your City, Postal Code</li>
        <li>T: +00 (0)00 0000</li>
        <li>F: +00 (0)00 0000</li>
        <li>E: info@LornoProductions.com</li>
        <li>www.LornoProductions.com</li>
      </ul>
      <div class="closing-rule"></div>
    </section>
  </main>
</body>
</html>
```